Stationery Design Project

I need a stationary design for our company. we are based in Houston, TX and we are called Mira Vell Lending. And we are wanting to brand our MoneyMendPlus program, which includes our tax preparation and restoration, credit repair service. Although our business offers other programs, we are interested in mainly focusing on The MoneyMendPlus program. We are looking for way to brand our ourselves and I believe that a great stationery design will help in achieving this goal. Our logo design is blue and light blue. the slogan is orange.

Industry/Entity Type

Business

Requirements
Must have
• Address: 30871 Calloway Ln. B-22
Houston, TX 75419
Tel. 555-318-6207
Fax 555-294-7153
www.miravelllending.example
info@miravelllending.example
Our Slogan: Happiness, Restored!

```html
<!DOCTYPE html>
<html lang="en">
<head>
<meta charset="utf-8">
<title>MoneyMendPlus Business Cards</title>
<link rel="stylesheet" href="https://fonts.googleapis.com/css2?family=Open+Sans:wght@400&family=Tinos:wght@400&display=swap">
<style>
  :root {
    --page: #ece6da;
    --white: #ffffff;
    --navy: #163e66;
    --brand-blue: #1f5fa8;
    --band-light: #1a9ad9;
    --band-dark: #1d4b9a;
    --gold: #f5a623;
    --sky: #0694d8;
    --deep: #1c3f8e;
    --pale: #cde4f5;
    --frame: #dfe9f2;
    --web-light: #d8ecf8;
  }
  * { margin: 0; padding: 0; box-sizing: border-box; }
  html, body { width: 1200px; height: 772px; overflow: hidden; }
  body { background: var(--page); position: relative; font-family: "Open Sans", sans-serif; }

  .card {
    position: absolute; width: 509px; height: 290px; border-radius: 18px;
    overflow: hidden; box-shadow: 4px 6px 10px rgba(0,0,0,.28);
  }
  .card--front { left: 83px; top: 80px; background: var(--white); }
  .card--back-blue { left: 628px; top: 78px; background: linear-gradient(90deg, var(--sky), var(--deep)); }
  .card--back-pale { left: 83px; top: 403px; background: var(--pale); }
  .card--back-white { left: 632px; top: 403px; background: var(--white); }

  .brand-name {
    position: absolute; left: 0; right: 0; text-align: center;
    font-family: "Tinos", serif; font-size: 46px; color: var(--brand-blue);
  }
  .card--front .brand-name { top: 86px; }
  .card--back-white .brand-name { top: 168px; }

  .contact-band {
    position: absolute; left: 0; right: 0; top: 162px; height: 87px;
    border-top: 3px solid var(--gold); border-bottom: 3px solid var(--gold);
    background: linear-gradient(90deg, var(--band-light), var(--band-dark));
    box-shadow: inset 0 2px 0 var(--white), inset 0 -2px 0 var(--white);
  }
  .contact-list {
    position: absolute; left: 29px; top: 12px; color: var(--white);
    font-size: 12px; line-height: 18px; list-style: none;
  }
  .contact-list .address { margin-top: 7px; }
  .slogan {
    position: absolute; right: 38px; top: 14px; text-align: center;
    font-family: "Tinos", serif; font-size: 25px; line-height: 29px;
    letter-spacing: 1px; text-transform: uppercase; color: var(--white);
  }

  .web {
    position: absolute; left: 0; right: 0; text-align: center;
    font-size: 12px; letter-spacing: 4.6px; color: var(--navy);
  }
  .card--front .web { top: 262px; }
  .card--back-blue .web { top: 240px; color: var(--web-light); }
  .card--back-pale .web, .card--back-white .web { top: 240px; }

  .badge {
    position: absolute; width: 152px; height: 152px; left: 50%; margin-left: -76px;
    background: var(--navy); border: 4px solid var(--frame);
    display: flex; align-items: flex-end; justify-content: center; padding-bottom: 30px;
    font-family: "Tinos", serif; font-size: 13px; color: var(--white);
  }
  .card--back-blue .badge { top: 50px; }
  .card--back-pale .badge { top: 50px; border-color: #9fb6c9; border-width: 3px; }
</style>
</head>
<body>
  <section class="card card--front">
    <div class="brand-name">MoneyMendPlus</div>
    <div class="contact-band">
      <ul class="contact-list">
        <li>T: 555-318-6207, F: 555-294-7153</li>
        <li>E: info@miravelllending.example</li>
        <li class="address">30871 Calloway Ln. B-22, Houston, TX 75419</li>
      </ul>
      <p class="slogan">Happiness,<br>Restored!</p>
    </div>
    <div class="web">www.miravelllending.example</div>
  </section>

  <section class="card card--back-blue">
    <div class="badge">Mira Vell Lending</div>
    <div class="web">www.miravelllending.example</div>
  </section>

  <section class="card card--back-pale">
    <div class="badge">Mira Vell Lending</div>
    <div class="web">www.miravelllending.example</div>
  </section>

  <section class="card card--back-white">
    <div class="brand-name">MoneyMendPlus</div>
    <div class="web">www.miravelllending.example</div>
  </section>
</body>
</html>
```